10-year customer thank you card

We want a greeting card that our sales reps can send to companies/customers who have been with our company for 10 or more years. We're a software company, our corporate color is blue but we also like green, orange, and purple. We'd like something rather minimal/simplistic for this card, perhaps building off our tree logo. We're really open to ideas for this one. You must use the template files that are uploaded. Copy included in 10 year thank you card file; the copy may change based on how it looks when laid out
Updates

I updated our brief. We'd prefer a sans serif font. I also uploaded a blank infographic image that includes more of our approved colors.

Industry/Entity Type

Software

Font styles to use
Sans Serif

```html
<!DOCTYPE html>
<html lang="en">
<head>
<meta charset="utf-8">
<title>Ten Year Thank You Card</title>
<link href="https://fonts.googleapis.com/css2?family=Arimo:wght@400;700&display=swap" rel="stylesheet">
<style>
  :root {
    --brand-orange: #f3733d;
    --paper: #ffffff;
    --ink: #222222;
    --tree-tone: #fbe3d8;
  }
  * { margin: 0; padding: 0; box-sizing: border-box; }
  html, body {
    width: 869px;
    height: 1200px;
    overflow: hidden;
    background: var(--paper);
    font-family: "Arimo", Arial, sans-serif;
  }
  .card {
    position: relative;
    width: 869px;
    height: 1200px;
    background: var(--paper);
  }

  /* Back of the folded card: header prints upside down */
  .back-header {
    position: absolute;
    left: 0;
    top: 0;
    width: 869px;
    height: 80px;
    transform: rotate(180deg);
  }
  .back-header .rule {
    position: absolute;
    left: 42px;
    right: 42px;
    top: 4px;
    height: 2px;
    background: var(--ink);
  }
  .company-name {
    position: absolute;
    left: 44px;
    top: 22px;
    display: flex;
    align-items: center;
    gap: 8px;
    font-size: 22px;
    font-weight: 400;
    color: var(--ink);
    letter-spacing: -0.2px;
  }
  .company-name .mark {
    width: 14px;
    height: 14px;
    background: var(--brand-orange);
  }
  .website {
    position: absolute;
    right: 42px;
    top: 20px;
    font-size: 24px;
    color: var(--brand-orange);
    letter-spacing: 0.5px;
  }

  /* Front of the folded card */
  .front-panel {
    position: absolute;
    left: 0;
    top: 600px;
    width: 869px;
    height: 600px;
    background: var(--brand-orange);
  }
  .years-badge {
    position: absolute;
    left: 679px;
    top: 23px;
    width: 159px;
    height: 184px;
    border: 2px solid var(--paper);
    color: var(--paper);
    text-align: center;
  }
  .years-badge .number {
    display: block;
    font-size: 118px;
    line-height: 1;
    margin-top: 10px;
    letter-spacing: -2px;
  }
  .years-badge .divider {
    display: block;
    width: 138px;
    height: 2px;
    margin: 11px auto 0;
    background: var(--paper);
  }
  .years-badge .label {
    display: block;
    font-size: 35px;
    line-height: 1;
    margin-top: 6px;
  }
  .tree-art {
    position: absolute;
    left: 344px;
    top: 133px;
    width: 283px;
    height: 277px;
  }
  .thank-you {
    position: absolute;
    left: 0;
    width: 869px;
    top: 433px;
    text-align: center;
    font-size: 66px;
    font-weight: 400;
    color: var(--paper);
    letter-spacing: -0.5px;
  }
</style>
</head>
<body>
  <div class="card">
    <header class="back-header">
      <div class="rule"></div>
      <div class="company-name"><span class="mark"></span>Cedarline Software</div>
      <div class="website">www.cedarline.com</div>
    </header>

    <section class="front-panel">
      <div class="years-badge">
        <span class="number">10</span>
        <span class="divider"></span>
        <span class="label">YEARS</span>
      </div>

      <svg class="tree-art" viewBox="0 0 283 277" role="img" aria-label="Stylised white zigzag tree illustration with a soft shadow at its base">
        <rect x="0" y="0" width="283" height="277" rx="6" fill="var(--tree-tone)" opacity="0.55"/>
      </svg>

      <h1 class="thank-you">Thank You</h1>
    </section>
  </div>
</body>
</html>
```